KLV Plant Services

We are a heavy diesel mechanical business with additional air con certificates, remapping engine rebuilt

Contact Information for Business Card

Company Name, Director Name, Managing Director, Contact details, email and website

Font styles to use
Serif
Script

```html
<!DOCTYPE html>
<html lang="en">
<head>
<meta charset="utf-8">
<title>KLV Plant Services – Business Card</title>
<link rel="stylesheet" href="https://fonts.googleapis.com/css2?family=Exo+2:wght@700;800&family=Montserrat:wght@400;500&display=swap">
<style>
  :root {
    --page: #2b2b2d;
    --card-dark: #1f1f21;
    --card-dark-edge: #333336;
    --art-light: #4a4a4e;
    --card-light: #ffffff;
    --navy: #2a2a6e;
    --ink: #2b2b2b;
    --muted: #3a3a3a;
    --white: #ffffff;
  }
  html, body {
    margin: 0;
    width: 1200px;
    height: 900px;
    overflow: hidden;
    background: var(--page);
  }
  .canvas {
    position: relative;
    width: 1200px;
    height: 900px;
  }
  .card {
    position: absolute;
    left: 320px;
    width: 560px;
    height: 320px;
    border-radius: 22px;
    box-shadow: 0 14px 34px rgba(0,0,0,.45);
    overflow: hidden;
  }
  .card--back {
    top: 90px;
    background: linear-gradient(135deg, var(--card-dark-edge), var(--card-dark) 60%);
  }
  .card--front {
    top: 470px;
    background: var(--card-light);
  }
  .backdrop-art {
    position: absolute;
    left: 110px;
    top: 26px;
    width: 300px;
    height: 180px;
    background: radial-gradient(ellipse at 60% 45%, var(--art-light), rgba(40,40,43,0) 70%);
  }
  .brand {
    position: absolute;
    display: flex;
    align-items: center;
    gap: 12px;
    font-family: "Exo 2", sans-serif;
    font-weight: 800;
    white-space: nowrap;
    line-height: 1;
  }
  .brand__dot {
    width: 18px;
    height: 18px;
    border-radius: 50%;
    flex: none;
  }
  .card--back .brand {
    right: 44px;
    top: 226px;
    font-size: 36px;
    color: var(--white);
  }
  .card--back .brand__dot { background: var(--white); }
  .card--front .brand {
    left: 0;
    right: 0;
    top: 46px;
    justify-content: center;
    font-size: 32px;
    color: var(--navy);
  }
  .card--front .brand__dot { background: var(--navy); }
  .person {
    position: absolute;
    right: 300px;
    top: 142px;
    text-align: right;
  }
  .person__name {
    margin: 0;
    font-family: "Exo 2", sans-serif;
    font-weight: 700;
    font-size: 26px;
    line-height: 1.1;
    letter-spacing: .5px;
    color: var(--navy);
  }
  .person__role {
    margin: 4px 0 0;
    font-family: "Montserrat", sans-serif;
    font-size: 15px;
    color: var(--muted);
  }
  .divider {
    position: absolute;
    left: 280px;
    top: 150px;
    width: 1.5px;
    height: 84px;
    background: var(--navy);
  }
  .contacts {
    position: absolute;
    left: 302px;
    top: 150px;
    margin: 0;
    padding: 0;
    list-style: none;
    font-family: "Montserrat", sans-serif;
    font-size: 14px;
    color: var(--ink);
  }
  .contacts li {
    display: flex;
    align-items: center;
    gap: 10px;
    height: 28px;
  }
  .contacts svg { width: 14px; height: 14px; fill: var(--navy); flex: none; }
  .address {
    position: absolute;
    left: 0;
    right: 0;
    bottom: 32px;
    margin: 0;
    text-align: center;
    font-family: "Montserrat", sans-serif;
    font-size: 14px;
    color: var(--ink);
  }
</style>
</head>
<body>
<main class="canvas">
  <section class="card card--back" aria-label="Card back">
    <div class="backdrop-art" role="img" aria-label="Dark excavator arm silhouette"></div>
    <div class="brand"><span class="brand__dot"></span>KLV Plant Services</div>
  </section>

  <section class="card card--front" aria-label="Card front">
    <div class="brand"><span class="brand__dot"></span>KLV Plant Services</div>

    <div class="person">
      <h1 class="person__name">DANIEL HARTWELL</h1>
      <p class="person__role">Managing Director</p>
    </div>

    <div class="divider"></div>

    <ul class="contacts">
      <li>
        <svg viewBox="0 0 24 24" aria-hidden="true"><path d="M6.6 10.8a15.1 15.1 0 0 0 6.6 6.6l2.2-2.2c.3-.3.7-.4 1-.2 1.1.4 2.3.6 3.6.6.6 0 1 .4 1 1V20c0 .6-.4 1-1 1A17 17 0 0 1 3 4c0-.6.4-1 1-1h3.5c.6 0 1 .4 1 1 0 1.3.2 2.5.6 3.6.1.3 0 .7-.2 1l-2.3 2.2z"/></svg>
        555-014-2297
      </li>
      <li>
        <svg viewBox="0 0 24 24" aria-hidden="true"><path d="M2 5h20v14H2V5zm2 2v.5l8 5 8-5V7H4zm16 2.8-8 5-8-5V17h16V9.8z"/></svg>
        info@klvplantservices.com
      </li>
      <li>
        <svg viewBox="0 0 24 24" aria-hidden="true"><path d="M12 2a10 10 0 1 0 0 20 10 10 0 0 0 0-20zm6.9 6h-3a15 15 0 0 0-1.3-3.9A8 8 0 0 1 18.9 8zM12 4c.8 1.2 1.5 2.5 1.9 4h-3.8c.4-1.5 1.1-2.8 1.9-4zM4.3 14a8 8 0 0 1 0-4h3.4a16 16 0 0 0 0 4H4.3zm.8 2h3a15 15 0 0 0 1.3 3.9A8 8 0 0 1 5.1 16zm3-8h-3a8 8 0 0 1 4.3-3.9C8.8 5.3 8.4 6.6 8.1 8zM12 20c-.8-1.2-1.5-2.5-1.9-4h3.8c-.4 1.5-1.1 2.8-1.900 4zm2.3-6H9.7a14 14 0 0 1 0-4h4.6a14 14 0 0 1 0 4zm.3 5.9c.6-1.2 1-2.5 1.3-3.9h3a8 8 0 0 1-4.3 3.9zm1.7-5.9a16 16 0 0 0 0-4h3.4a8 8 0 0 1 0 4h-3.4z"/></svg>
        www.klvplantservices.com
      </li>
    </ul>

    <p class="address">P.O. Box 48 Ridge Road Northfield AB, T4B 2K1</p>
  </section>
</main>
</body>
</html>
```